Harbor Crestline (Business Card Design)

Need business cards designed. Something modern, chic, and sleek. Mabye the back of the card should be the navy blue that is in the logo and then just the logo on the back.

Target Market(s)

Those in the hotel, office, and renovation industry

Contact Information for Business Card

1. Logo 2. Dorian Fenwick 3. CEO/Founder 4. Phone: (833) HarbCre / (833) 427-2731 5. Email: dorian@theharborcrestline.com 6. Website: www.theharborcrestline.com

Font styles to use
Other font styles liked:
• Look at the logo font and base the font for everything else off of that.

Colors
0054AA
0677BA
7BADD7
CADEEF
E8F1F8

Requirements
Must have
• Colors that are associated in the logo
Nice to have
• Sleek modern clean and chic design.

```html
<!DOCTYPE html>
<html lang="en">
<head>
<meta charset="utf-8">
<title>Harbor Crestline – Business Card</title>
<link href="https://fonts.googleapis.com/css2?family=Montserrat:wght@600;700&family=Open+Sans:wght@400;600;700&display=swap" rel="stylesheet">
<style>
  :root {
    --backdrop: #202124;
    --navy: #0c1741;
    --navy-deep: #08102f;
    --navy-light: #1b2a66;
    --gold: #c9a04a;
    --white: #ffffff;
    --divider: rgba(255,255,255,0.45);
  }
  * { margin: 0; padding: 0; box-sizing: border-box; }
  html, body {
    width: 1200px; height: 780px; overflow: hidden;
    background: var(--backdrop);
  }
  .canvas {
    position: relative; width: 1200px; height: 780px;
    display: flex; align-items: center; justify-content: center; gap: 50px;
  }
  .card {
    position: relative; width: 525px; height: 300px;
    background: var(--navy); overflow: hidden;
    box-shadow: 0 14px 30px rgba(0,0,0,0.45);
  }

  /* Front */
  .brand {
    position: absolute; left: 48px; top: 62px;
    display: flex; align-items: center; gap: 12px;
  }
  .brand-square { width: 18px; height: 18px; background: var(--white); flex: none; }
  .brand-name {
    font-family: "Montserrat", sans-serif; font-weight: 700;
    font-size: 23px; line-height: 1.1; letter-spacing: 1.5px;
    color: var(--white); text-transform: uppercase; white-space: nowrap;
  }
  .divider {
    position: absolute; left: 0; top: 0; width: 525px; height: 300px;
  }
  .person { position: absolute; left: 276px; top: 70px; }
  .person-name {
    font-family: "Open Sans", sans-serif; font-weight: 700;
    font-size: 30px; line-height: 1; color: var(--white); white-space: nowrap;
  }
  .person-name .first { color: var(--gold); }
  .person-title {
    margin-top: 6px;
    font-family: "Open Sans", sans-serif; font-weight: 400;
    font-size: 15px; color: var(--white);
  }
  .contacts { position: absolute; left: 240px; top: 148px; list-style: none; }
  .contacts li {
    display: flex; align-items: center; gap: 8px;
    font-family: "Open Sans", sans-serif; font-size: 12.5px;
    color: var(--white); line-height: 20px; white-space: nowrap;
  }
  .contacts svg { width: 11px; height: 11px; flex: none; }
  .address-band {
    position: absolute; left: 0; bottom: 22px; width: 418px; height: 28px;
    background: var(--gold);
    display: flex; align-items: center; padding-left: 42px;
    font-family: "Open Sans", sans-serif; font-size: 13.5px; color: var(--white);
    white-space: nowrap;
  }
  .corner-tail { position: absolute; right: 0; bottom: 0; width: 120px; height: 60px; }
  .corner-mark {
    position: absolute; right: 16px; bottom: 68px;
    font-family: "Montserrat", sans-serif; font-weight: 700;
    font-size: 9px; letter-spacing: 1px; color: var(--white);
    text-transform: uppercase; white-space: nowrap;
  }

  /* Back */
  .card-back {
    background: linear-gradient(120deg, var(--navy-deep) 0%, var(--navy) 55%, var(--navy-light) 100%);
  }
  .back-texture {
    position: absolute; inset: 0;
    background: radial-gradient(ellipse at 90% 80%, rgba(160,170,220,0.22), transparent 60%);
  }
  .back-brand {
    position: absolute; inset: 0;
    display: flex; align-items: center; justify-content: center; gap: 16px;
  }
  .back-brand .brand-square { width: 26px; height: 26px; }
  .back-brand .brand-name { font-size: 34px; letter-spacing: 3px; }
</style>
</head>
<body>
<main class="canvas">

  <section class="card card-front" aria-label="Card front">
    <div class="brand">
      <span class="brand-square"></span>
      <span class="brand-name">Harbor<br>Crestline</span>
    </div>

    <svg class="divider" viewBox="0 0 525 300" aria-hidden="true">
      <line x1="222" y1="168" x2="262" y2="70" stroke="var(--divider)" stroke-width="1"/>
    </svg>

    <div class="person">
      <h1 class="person-name"><span class="first">Dorian</span> Fenwick</h1>
      <p class="person-title">CEO/Founder</p>
    </div>

    <ul class="contacts">
      <li>
        <svg viewBox="0 0 12 12" aria-hidden="true"><path d="M2.5 1h2l1 2.5-1.3 1a6 6 0 0 0 3.3 3.3l1-1.3L11 7.5v2A1.5 1.5 0 0 1 9.5 11 8.5 8.5 0 0 1 1 2.5 1.5 1.5 0 0 1 2.5 1z" fill="var(--gold)"/></svg>
        (833) HarbCre / (833) 427-2731
      </li>
      <li>
        <svg viewBox="0 0 12 12" aria-hidden="true"><circle cx="6" cy="6" r="5" fill="none" stroke="var(--gold)" stroke-width="1.3"/><path d="M1 6h10M6 1c-2.5 3-2.5 7 0 10M6 1c2.5 3 2.5 7 0 10" fill="none" stroke="var(--gold)" stroke-width="1"/></svg>
        www.theharborcrestline.com
      </li>
      <li>
        <svg viewBox="0 0 12 12" aria-hidden="true"><rect x="1" y="2.5" width="10" height="7" fill="var(--gold)"/><path d="M1 2.5l5 4 5-4" fill="none" stroke="var(--navy)" stroke-width="1"/></svg>
        dorian@theharborcrestline.com
      </li>
    </ul>

    <div class="address-band">4120 Lakeview Pkwy Suite 210, Easton, MD 21601</div>
    <svg class="corner-tail" viewBox="0 0 120 60" aria-hidden="true">
      <polygon points="60,60 120,0 120,60" fill="var(--white)"/>
    </svg>
    <span class="corner-mark">Harbor Crestline</span>
  </section>

  <section class="card card-back" aria-label="Card back">
    <div class="back-texture" role="img" aria-label="Subtle repeating brand-mark pattern in navy with a soft silver sheen"></div>
    <div class="back-brand">
      <span class="brand-square"></span>
      <span class="brand-name">Harbor Crestline</span>
    </div>
  </section>

</main>
</body>
</html>
```